VANTOL GROUP

This is a company that provides executive protection. Our motto is "New Era in Protection"... I don't want this to look like other security websites. I want it to be clean and sharp and represent a new era. We are based in the bay area so maybe a picture of San Francisco in the background?
I want it to be able to funnel down a couple different categories.
1. About Us
2. Services (Executive Protection, Covert Protection, Residential Protection & Intelligence)
3. Blue Maple (Training & Consulting)
4. Contact Us
I want it to be very clean and modern. I don't want there to be any pictures of bodyguards with ear pieces like every other website.
Target Market(s)
Ultra High Net Worth Individuals
Coding
Coded - Design and coding required
Number of Pages Required
1 page
Requirements
Must have
- Colors of my Symbol
Nice to have
- City in the background, San Francisco, New York or the Pinecrest Lodge in Montana.
Should not have
- Should not look like an KVM website or have photos of bodyguards. I want this to be a clean and simple website with my logo

```html
<!DOCTYPE html>
<html lang="en">
<head>
<meta charset="utf-8">
<title>Vantol Group — New Era in Protection</title>
<link rel="stylesheet" href="https://fonts.googleapis.com/css2?family=Roboto:wght@400;500;700&family=Titillium+Web:wght@700&display=swap">
<style>
:root{
  --red:#8c1619;
  --red-dark:#6f1013;
  --ink:#1d1d1f;
  --text:#666668;
  --hex-grey:#6a6a6e;
  --panel:#f4f4f4;
  --contact:#6c6d71;
  --white:#ffffff;
  --head:"Titillium Web",sans-serif;
  --body:"Roboto",sans-serif;
}
*{box-sizing:border-box;margin:0;padding:0}
html,body{width:1200px;height:3218px;overflow:hidden}
body{font-family:var(--body);color:var(--ink);background:var(--white);position:relative}
section,header,footer{position:absolute;left:0;width:1200px}

/* header */
.site-header{top:0;height:86px;background:var(--white);z-index:3;border-bottom:1px solid #e4e4e4}
.brand-tab{position:absolute;left:112px;top:0;width:208px;height:145px;background:var(--white);
  clip-path:polygon(0 0,100% 0,100% 59%,88% 100%,12% 100%,0 59%)}
.brand-mark{position:absolute;left:86px;top:30px;width:36px;height:36px;background:var(--red)}
.brand-name{position:absolute;left:0;top:94px;width:208px;text-align:center;font-family:var(--body);
  font-weight:700;font-size:21px;letter-spacing:1px;color:var(--ink);white-space:nowrap}
.main-nav{position:absolute;top:33px;left:0;width:1200px;height:20px}
.main-nav a{position:absolute;transform:translateX(-50%);font-size:15px;font-weight:500;color:var(--ink);text-decoration:none;white-space:nowrap}
.main-nav a.active{color:var(--red)}
.search-icon{position:absolute;left:933px;top:36px}
.login-btn{position:absolute;left:978px;top:24px;width:110px;height:36px;border-radius:18px;background:var(--red);
  color:var(--white);font-size:15px;font-weight:500;display:flex;align-items:center;justify-content:center;gap:7px}

/* hero */
.hero{top:86px;height:600px;overflow:hidden}
.hero-photo{position:absolute;inset:0;
  background:
  linear-gradient(180deg,rgba(20,24,40,0) 62%,rgba(15,20,35,.55) 100%),
  radial-gradient(ellipse 30% 10% at 78% 70%,rgba(255,190,120,.55),transparent 70%),
  radial-gradient(ellipse 45% 8% at 30% 42%,rgba(255,200,130,.5),transparent 70%),
  radial-gradient(ellipse 55% 18% at 62% 32%,rgba(240,170,110,.55),transparent 72%),
  radial-gradient(ellipse 25% 14% at 10% 30%,rgba(220,160,110,.45),transparent 70%),
  linear-gradient(180deg,#5b6a8c 0%,#7b7a8e 14%,#6a5a68 26%,#55463f 38%,#3d3540 48%,#2c3550 62%,#3a4a6c 74%,#28304a 100%)}
.hero-content{position:absolute;left:0;top:0;width:1200px;text-align:center;color:var(--white)}
.hero-title{position:absolute;left:0;width:1200px;top:199px;font-family:var(--head);font-size:50px;letter-spacing:1px;line-height:1;text-shadow:0 2px 8px rgba(0,0,0,.35)}
.hero-sub{position:absolute;left:350px;width:500px;top:270px;font-size:17px;font-weight:500;line-height:27px;text-shadow:0 1px 4px rgba(0,0,0,.5)}
.btn{display:inline-flex;align-items:center;justify-content:center;gap:8px;border-radius:28px;font-weight:700;text-transform:uppercase}
.btn-red{background:var(--red);color:var(--white)}
.hero .btn{position:absolute;left:504px;top:342px;width:192px;height:46px;font-size:16px}
.hero-arrow{position:absolute;top:281px;width:36px;height:36px}

/* about */
.about{top:686px;height:591px}
.about-visual{position:absolute;left:110px;top:76px;width:404px;height:427px;
  background:
  radial-gradient(circle at 72% 22%,rgba(230,170,175,.45),transparent 22%),
  radial-gradient(circle at 25% 70%,rgba(200,130,135,.35),transparent 25%),
  radial-gradient(ellipse 70% 50% at 50% 40%,#8e4a51 0%,#6d2e34 50%,#4a1c22 100%)}
.section-title{font-family:var(--head);font-size:42px;line-height:1;letter-spacing:.5px;color:var(--ink)}
.about .section-title{position:absolute;left:600px;top:108px}
.about-copy{position:absolute;left:600px;top:169px;width:480px;font-size:14.5px;line-height:24px;color:var(--text)}
.about-copy p+p{margin-top:11px}
.about .btn{position:absolute;left:600px;top:379px;width:155px;height:41px;font-size:14px}

/* services */
.services{top:1277px;height:587px;background:radial-gradient(ellipse 55% 35% at 50% 55%,#e6e6e6,var(--panel) 70%)}
.services .section-title{position:absolute;left:0;width:1200px;text-align:center;top:55px}
.service{position:absolute;top:134px;width:301px;height:347px;color:var(--white);text-align:center}
.service svg.hex{position:absolute;inset:0}
.service .icon{position:absolute;left:120px;top:52px}
.service h3{position:absolute;left:20px;width:261px;top:142px;font-size:18px;font-weight:700;line-height:26px}
.service p{position:absolute;left:38px;width:225px;font-size:14px;line-height:20px}
.service .more{position:absolute;left:129px;top:257px}

/* about band */
.about-band{top:1864px;height:482px;background:var(--red);overflow:hidden}
.about-band-photo{position:absolute;inset:0;clip-path:polygon(597px 0,1200px 0,1200px 482px,680px 482px);
  background:
  radial-gradient(ellipse 18% 30% at 78% 55%,rgba(150,150,155,.6),transparent 70%),
  radial-gradient(ellipse 16% 30% at 62% 60%,rgba(70,80,85,.55),transparent 70%),
  radial-gradient(ellipse 30% 20% at 85% 92%,rgba(240,235,225,.8),transparent 70%),
  linear-gradient(180deg,#e4e2de 0%,#cfc9c0 40%,#a39a8f 75%,#d8d2c8 100%)}
.about-band .section-title{position:absolute;left:110px;top:80px;color:var(--white)}
.about-band-copy{position:absolute;left:110px;top:143px;width:465px;font-size:14.5px;line-height:24px;color:var(--white)}
.about-band-copy p+p{margin-top:10px}
.btn-white{background:var(--white);color:var(--red)}
.about-band .btn{position:absolute;left:110px;top:354px;width:162px;height:44px;font-size:14px}

/* contact */
.contact{top:2346px;height:495px;background:radial-gradient(ellipse 60% 25% at 50% 62%,#86878b,var(--contact) 70%)}
.contact .section-title{position:absolute;left:0;width:1200px;text-align:center;top:65px;color:var(--white)}
.field{position:absolute;border:2px solid rgba(255,255,255,.42);border-radius:27px;color:var(--white);font-size:14px;padding:0 0 0 28px;display:flex;align-items:center}
.field.input{left:191px;width:393px;height:52px}
.field.message{left:607px;top:145px;width:397px;height:186px;align-items:flex-start;padding-top:26px;border-radius:24px}
.contact .btn{position:absolute;left:498px;top:372px;width:205px;height:52px;font-size:16px}

/* footer */
.site-footer{top:2841px;height:377px;background:var(--white)}
.footer-brand{position:absolute;left:134px;top:78px;width:194px;height:130px}
.footer-brand .brand-mark{left:77px;top:10px;width:40px;height:40px}
.footer-brand .brand-name{left:0;top:86px;width:194px;font-size:22px}
.social{position:absolute;top:233px;width:36px;height:36px;border-radius:50%;background:#e6e6e6;display:flex;align-items:center;justify-content:center}
.footer-col{position:absolute;top:80px}
.footer-col h4{font-size:18px;font-weight:700;color:var(--ink);margin-bottom:14px}
.footer-col li{list-style:none;font-size:13.5px;color:#555;height:32.5px;display:flex;align-items:flex-start;gap:10px}
.footer-col li .chev{color:var(--red);font-size:12px;line-height:17px}
.footer-col.contact-info li{gap:10px;height:auto;margin-bottom:14px;line-height:23px}
.footer-divider{position:absolute;left:110px;top:305px;width:980px;height:1px;background:#e2e2e2}
.copyright{position:absolute;left:0;width:1200px;top:331px;text-align:center;font-size:13.5px;color:#555}
.chat-bubble{position:absolute;left:1120px;top:285px;width:38px;height:38px;border-radius:50%;background:var(--red);display:flex;align-items:center;justify-content:center}
</style>
</head>
<body>

<header class="site-header">
  <div class="brand-tab">
    <span class="brand-mark"></span>
    <span class="brand-name">VANTOL GROUP</span>
  </div>
  <nav class="main-nav">
    <a class="active" style="left:504px">Home</a>
    <a style="left:587px">About Us</a>
    <a style="left:679px">Services</a>
    <a style="left:768px">Blue Maple</a>
    <a style="left:865px">Contact Us</a>
  </nav>
  <svg class="search-icon" width="15" height="15" viewBox="0 0 15 15" aria-hidden="true"><circle cx="6" cy="6" r="4.6" fill="none" stroke="#1d1d1f" stroke-width="2"/><path d="M9.5 9.5l4 4" stroke="#1d1d1f" stroke-width="2.2" stroke-linecap="round"/></svg>
  <div class="login-btn">
    <svg width="11" height="13" viewBox="0 0 11 13" aria-hidden="true"><path d="M2.5 6V4a3 3 0 016 0v2" fill="none" stroke="#fff" stroke-width="1.8"/><rect x="0.5" y="6" width="10" height="7" rx="1" fill="#fff"/></svg>
    Login
  </div>
</header>

<section class="hero">
  <div class="hero-photo" role="img" aria-label="Aerial night view of the San Francisco skyline and the Bay Bridge with city lights"></div>
  <div class="hero-content">
    <h1 class="hero-title">VANTOL GROUP</h1>
    <p class="hero-sub">Lorem ipsum dolor sit amet, consectetur adipiscing elit, sed do eiusmod tempor incididunt labore magna aliqua.</p>
    <a class="btn btn-red">Get Started
      <svg width="15" height="15" viewBox="0 0 16 16" aria-hidden="true"><circle cx="8" cy="8" r="8" fill="#fff"/><path d="M6.5 4.5L10 8l-3.5 3.5" fill="none" stroke="#8c1619" stroke-width="2.2"/></svg>
    </a>
  </div>
  <svg class="hero-arrow" style="left:36px" viewBox="0 0 36 36" aria-hidden="true"><circle cx="18" cy="18" r="16.5" fill="none" stroke="#fff" stroke-width="1.8"/><path d="M21 11l-7 7 7 7" fill="none" stroke="#fff" stroke-width="2"/></svg>
  <svg class="hero-arrow" style="left:1128px" viewBox="0 0 36 36" aria-hidden="true"><circle cx="18" cy="18" r="16.5" fill="none" stroke="#fff" stroke-width="1.8"/><path d="M15 11l7 7-7 7" fill="none" stroke="#fff" stroke-width="2"/></svg>
</section>

<section class="about">
  <div class="about-visual" role="img" aria-label="Deep red duotone aerial view of a city at dusk with glowing network lines"></div>
  <h2 class="section-title">ABOUT US</h2>
  <div class="about-copy">
    <p>Lorem ipsum dolor sit amet, consectetur adipiscing elit, sed do eiusmod tempor incididunt ut labore et dolore magna aliqua. Ut enim ad minim veniam, quis nostrud exercitation ullamco laboris nisi ut aliquip ex ea commodo consequat. Duis aute irure dolor in reprehenderit in voluptate velit esse cillum dolore eu fugiat nulla pariatur.</p>
    <p>&nbsp;Excepteur sint occaecat cupidatat non proident, sunt in culpa qui officia deserunt mollit anim id est laborum.</p>
  </div>
  <a class="btn btn-red">Read More
    <svg width="13" height="13" viewBox="0 0 16 16" aria-hidden="true"><circle cx="8" cy="8" r="8" fill="#fff"/><path d="M6.5 4.5L10 8l-3.5 3.5" fill="none" stroke="#8c1619" stroke-width="2.2"/></svg>
  </a>
</section>

<section class="services">
  <h2 class="section-title">OUR SERVICES</h2>

  <article class="service" style="left:112px">
    <svg class="hex" viewBox="0 0 301 347" aria-hidden="true"><polygon points="150.5,0 301,75 301,272 150.5,347 0,272 0,75" fill="#6a6a6e"/></svg>
    <svg class="icon" width="62" height="62" viewBox="0 0 62 62" aria-hidden="true"><path d="M31 4l22 8v17c0 15-10 25-22 29C19 54 9 44 9 29V12z" fill="none" stroke="#fff" stroke-width="2.4"/><path d="M22 31l7 7 12-14" fill="none" stroke="#fff" stroke-width="2.4"/></svg>
    <h3>Executive Protection</h3>
    <p style="top:185px">Lorem ipsum dolor sit amet, consectetur adipiscing elit, sed do tempor incididunt ut et</p>
    <svg class="more" width="43" height="43" viewBox="0 0 43 43" aria-hidden="true"><circle cx="21.5" cy="21.5" r="20" fill="none" stroke="#fff" stroke-width="2"/><path d="M14 18l7.5 7.5L29 18" fill="none" stroke="#fff" stroke-width="2.2"/></svg>
  </article>

  <article class="service" style="left:450px">
    <svg class="hex" viewBox="0 0 301 347" aria-hidden="true"><polygon points="150.5,0 301,75 301,272 150.5,347 0,272 0,75" fill="#8c1619"/></svg>
    <svg class="icon" width="62" height="62" viewBox="0 0 62 62" aria-hidden="true"><rect x="14" y="27" width="34" height="26" rx="3" fill="none" stroke="#fff" stroke-width="2.4"/><path d="M21 27v-7a10 10 0 0120 0v7" fill="none" stroke="#fff" stroke-width="2.4"/><circle cx="31" cy="39" r="3.5" fill="#fff"/><path d="M31 42v5" stroke="#fff" stroke-width="2.4"/></svg>
    <h3>Covert Protection</h3>
    <p style="top:185px">Lorem ipsum dolor sit amet, consectetur adipiscing elit, sed do tempor incididunt ut et</p>
    <svg class="more" width="43" height="43" viewBox="0 0 43 43" aria-hidden="true"><circle cx="21.5" cy="21.5" r="20" fill="none" stroke="#fff" stroke-width="2"/><path d="M14 18l7.5 7.5L29 18" fill="none" stroke="#fff" stroke-width="2.2"/></svg>
  </article>

  <article class="service" style="left:788px">
    <svg class="hex" viewBox="0 0 301 347" aria-hidden="true"><polygon points="150.5,0 301,75 301,272 150.5,347 0,272 0,75" fill="#6a6a6e"/></svg>
    <svg class="icon" width="62" height="62" viewBox="0 0 62 62" aria-hidden="true"><path d="M8 30L31 10l23 20" fill="none" stroke="#fff" stroke-width="2.4"/><path d="M14 25v28h34V25" fill="none" stroke="#fff" stroke-width="2.4"/><rect x="26" y="37" width="10" height="16" fill="none" stroke="#fff" stroke-width="2.4"/></svg>
    <h3>Residential Protection<br>&amp; Intelligence</h3>
    <p style="top:211px">Lorem ipsum dolor sit amet, consectetur adipiscing</p>
    <svg class="more" width="43" height="43" viewBox="0 0 43 43" aria-hidden="true"><circle cx="21.5" cy="21.5" r="20" fill="none" stroke="#fff" stroke-width="2"/><path d="M14 18l7.5 7.5L29 18" fill="none" stroke="#fff" stroke-width="2.2"/></svg>
  </article>
</section>

<section class="about-band">
  <div class="about-band-photo" role="img" aria-label="Team of colleagues working together around a laptop in a bright office"></div>
  <h2 class="section-title">ABOUT US</h2>
  <div class="about-band-copy">
    <p>Sed ut perspiciatis unde omnis iste natus errorvoluptatem accusantium doloremque laudantium, totam rem aperiam, eaque ipsa quae ab illo inventore veritatis et quasi architecto beatae vitae dicta sunt explicabo.</p>
    <p>Lorem ipsum dolor sit amet, consectetur adipiscing elit, sed do eiusmod tempor incididunt ut labore et dolore magna aliqua. Ut enim ad minim veniam, quis nostrud exercitation ullamco</p>
  </div>
  <a class="btn btn-white">Learn More
    <svg width="13" height="13" viewBox="0 0 16 16" aria-hidden="true"><circle cx="8" cy="8" r="8" fill="#8c1619"/><path d="M6.5 4.5L10 8l-3.5 3.5" fill="none" stroke="#fff" stroke-width="2.2"/></svg>
  </a>
</section>

<section class="contact">
  <h2 class="section-title">CONTACT US</h2>
  <div class="field input" style="top:146px">Name</div>
  <div class="field input" style="top:211px">Email Address</div>
  <div class="field input" style="top:276px">Phone Number</div>
  <div class="field message">Message</div>
  <a class="btn btn-red">Submit Now
    <svg width="15" height="15" viewBox="0 0 16 16" aria-hidden="true"><circle cx="8" cy="8" r="8" fill="#fff"/><path d="M6.5 4.5L10 8l-3.5 3.5" fill="none" stroke="#8c1619" stroke-width="2.2"/></svg>
  </a>
</section>

<footer class="site-footer">
  <div class="footer-brand">
    <span class="brand-mark"></span>
    <span class="brand-name">VANTOL GROUP</span>
  </div>
  <span class="social" style="left:148px" aria-label="Social profile"><svg width="14" height="14" viewBox="0 0 14 14" aria-hidden="true"><circle cx="7" cy="7" r="3" fill="#1d1d1f"/></svg></span>
  <span class="social" style="left:191px" aria-label="Social profile"><svg width="14" height="14" viewBox="0 0 14 14" aria-hidden="true"><circle cx="7" cy="7" r="3" fill="#1d1d1f"/></svg></span>
  <span class="social" style="left:233px" aria-label="Social profile"><svg width="14" height="14" viewBox="0 0 14 14" aria-hidden="true"><circle cx="7" cy="7" r="3" fill="#1d1d1f"/></svg></span>
  <span class="social" style="left:277px" aria-label="Social profile"><svg width="14" height="14" viewBox="0 0 14 14" aria-hidden="true"><circle cx="7" cy="7" r="3" fill="#1d1d1f"/></svg></span>

  <div class="footer-col" style="left:427px">
    <h4>Quick Links</h4>
    <ul>
      <li><span class="chev">»</span>Home</li>
      <li><span class="chev">»</span>About Us</li>
      <li><span class="chev">»</span>Services</li>
      <li><span class="chev">»</span>Blue Maple</li>
      <li><span class="chev">»</span>Contact Us</li>
    </ul>
  </div>
  <div class="footer-col" style="left:643px">
    <h4>Important</h4>
    <ul>
      <li><span class="chev">»</span>Terms of Use</li>
      <li><span class="chev">»</span>Site Map</li>
      <li><span class="chev">»</span>Privacy Policy</li>
      <li><span class="chev">»</span>Disclaimer</li>
    </ul>
  </div>
  <div class="footer-col contact-info" style="left:863px">
    <h4>Contact us</h4>
    <ul>
      <li><svg width="10" height="14" viewBox="0 0 10 14" aria-hidden="true" style="margin-top:5px;flex:none"><path d="M5 0a5 5 0 015 5c0 4-5 9-5 9S0 9 0 5a5 5 0 015-5z" fill="#8c1619"/><circle cx="5" cy="5" r="2" fill="#fff"/></svg><span>1/155 Lorem ipsum dolor sit amet,<br>consectetur adipiscing elit,</span></li>
      <li><svg width="10" height="14" viewBox="0 0 10 14" aria-hidden="true" style="margin-top:4px;flex:none"><rect x="1" y="0.8" width="8" height="12.4" rx="1.5" fill="none" stroke="#8c1619" stroke-width="1.6"/><circle cx="5" cy="10.5" r="1" fill="#8c1619"/></svg><span>&nbsp;+555-555-5555</span></li>
      <li><svg width="14" height="13" viewBox="0 0 14 13" aria-hidden="true" style="margin-top:5px;flex:none"><rect x="0" y="4" width="14" height="9" rx="1" fill="#8c1619"/><rect x="3" y="0" width="8" height="5" fill="none" stroke="#8c1619" stroke-width="1.5"/></svg><span>+ 123 456 7892</span></li>
      <li><svg width="14" height="11" viewBox="0 0 14 11" aria-hidden="true" style="margin-top:6px;flex:none"><rect x="0.8" y="0.8" width="12.4" height="9.4" fill="none" stroke="#8c1619" stroke-width="1.5"/><path d="M1 1l6 5 6-5" fill="none" stroke="#8c1619" stroke-width="1.5"/></svg><span>info@Vantol Group.com</span></li>
    </ul>
  </div>
  <div class="footer-divider"></div>
  <p class="copyright">© 2021&nbsp; Vantol Group &nbsp;|&nbsp; All Rights Reserved</p>
  <div class="chat-bubble" aria-label="Chat">
    <svg width="18" height="16" viewBox="0 0 18 16" aria-hidden="true"><path d="M9 1c4.4 0 8 2.8 8 6.2s-3.6 6.2-8 6.2c-1 0-2-.1-2.9-.4L2 15l1.2-3.4C1.8 10.5 1 9 1 7.2 1 3.8 4.6 1 9 1z" fill="#fff"/><circle cx="5.5" cy="7.2" r="1" fill="#8c1619"/><circle cx="9" cy="7.2" r="1" fill="#8c1619"/><circle cx="12.5" cy="7.2" r="1" fill="#8c1619"/></svg>
  </div>
</footer>

</body>
</html>
```